Company Mission & Values Poster

I'd like an A2 Portrait Poster displaying our company's Mission & Values.
See our website for our logo, fonts, mission & values.
https://valdintor.com.au/

Our Mission: Creating homes for abundant life
Values: Love, Thinking, Team, Zoe.

Some ideas to consider:
Mission as the Headline then
A logo for each of the 4 Values and the words

Target Market(s)

Myself & my team

Industry/Entity Type

Real Estate

Font styles to use
Other font styles liked:
• Company fonts as seen on our website

```html
<!DOCTYPE html>
<html lang="en">
<head>
<meta charset="utf-8">
<title>Valdintor — Mission &amp; Values</title>
<link rel="stylesheet" href="https://fonts.googleapis.com/css2?family=Jost:wght@400;500&family=Playfair+Display:ital,wght@1,500&display=swap">
<style>
  :root {
    --forest: #0f3b30;
    --ink-white: #f4f4f0;
    --heart-red: #e3141b;
    --bulb-orange: #f39a1e;
    --smile-yellow: #f5c52a;
    --accent-green: #3fbf4a;
  }
  * { margin: 0; padding: 0; box-sizing: border-box; }
  html, body { width: 975px; height: 1200px; overflow: hidden; background: var(--forest); }
  .poster {
    position: relative;
    width: 975px;
    height: 1200px;
    background: var(--forest);
    color: var(--ink-white);
    font-family: "Jost", sans-serif;
  }
  .mission {
    position: absolute;
    top: 138px;
    left: 0;
    width: 100%;
    text-align: center;
    font-weight: 400;
    font-size: 49px;
    line-height: 70px;
    letter-spacing: 0.5px;
  }
  .mission em {
    font-family: "Playfair Display", serif;
    font-style: italic;
    font-weight: 500;
    font-size: 56px;
  }
  .values-map { position: absolute; inset: 0; }
  .value-label {
    font-family: "Jost", sans-serif;
    font-size: 37px;
    fill: var(--ink-white);
    text-anchor: middle;
    letter-spacing: 0.5px;
  }
  .brand-name {
    position: absolute;
    left: 90px;
    top: 1112px;
    font-size: 32px;
    font-weight: 400;
    letter-spacing: 5px;
  }
  .web-address {
    position: absolute;
    right: 86px;
    top: 1120px;
    font-size: 27px;
    letter-spacing: 0.3px;
  }
</style>
</head>
<body>
<main class="poster">
  <h1 class="mission">Creating Home<br>for <em>Abundant Life</em></h1>

  <svg class="values-map" viewBox="0 0 975 1200" width="975" height="1200">
    <!-- divider dots -->
    <g class="divider" fill="var(--ink-white)">
      <circle cx="396" cy="340" r="1.8"/><circle cx="411" cy="340" r="1.8"/><circle cx="426" cy="340" r="1.8"/>
      <circle cx="441" cy="340" r="1.8"/><circle cx="456" cy="340" r="1.8"/><circle cx="471" cy="340" r="1.8"/>
      <circle cx="486" cy="340" r="1.8"/><circle cx="501" cy="340" r="1.8"/><circle cx="516" cy="340" r="1.8"/>
      <circle cx="531" cy="340" r="1.8"/><circle cx="546" cy="340" r="1.8"/><circle cx="561" cy="340" r="1.8"/>
      <circle cx="576" cy="340" r="1.8"/>
    </g>

    <!-- orbit lines -->
    <g class="orbits" fill="none" stroke="var(--ink-white)" stroke-width="7" stroke-linecap="butt">
      <path d="M240 498 A246.5 201 0 0 0 733 498"/>
      <path d="M133 498 A370 345 0 0 0 840 517"/>
      <path d="M202 793 Q546 960 666 842"/>
    </g>

    <!-- value: Thinking -->
    <g class="value value-thinking">
      <circle cx="483" cy="505" r="62" fill="var(--ink-white)"/>
      <circle cx="483" cy="505" r="32" fill="var(--bulb-orange)" role="img" aria-label="Light bulb icon"/>
      <text class="value-label" x="484" y="620">Thinking</text>
    </g>

    <!-- value: Love -->
    <g class="value value-love">
      <circle cx="176" cy="653" r="72" fill="var(--forest)"/>
      <circle cx="176" cy="653" r="62" fill="var(--ink-white)"/>
      <path d="M176 691 C150 670 134 656 134 637 C134 623 145 613 157 613 C166 613 172 618 176 625 C180 618 186 613 195 613 C207 613 218 623 218 637 C218 656 202 670 176 691 Z" fill="var(--heart-red)"/>
      <text class="value-label" x="174" y="748">Love</text>
    </g>

    <!-- value: Team -->
    <g class="value value-team">
      <circle cx="742" cy="710" r="72" fill="var(--forest)"/>
      <circle cx="742" cy="710" r="62" fill="var(--ink-white)"/>
      <circle cx="742" cy="712" r="30" fill="var(--heart-red)" role="img" aria-label="Team member icon"/>
      <text class="value-label" x="737" y="810">Team</text>
    </g>

    <!-- value: Zoe -->
    <g class="value value-zoe">
      <circle cx="490" cy="889" r="72" fill="var(--forest)"/>
      <circle cx="490" cy="889" r="62" fill="var(--ink-white)"/>
      <circle cx="490" cy="889" r="38" fill="var(--smile-yellow)" role="img" aria-label="Smiling emoji icon"/>
      <text class="value-label" x="495" y="992">Zoe</text>
    </g>

    <!-- footer accent dots -->
    <g class="footer-dots" fill="var(--accent-green)">
      <circle cx="802" cy="1104" r="1.8"/><circle cx="818" cy="1104" r="1.8"/><circle cx="835" cy="1104" r="1.8"/>
      <circle cx="851" cy="1104" r="1.8"/><circle cx="868" cy="1104" r="1.8"/><circle cx="885" cy="1104" r="1.8"/>
    </g>
  </svg>

  <div class="brand-name">VALDINTOR</div>
  <div class="web-address">valdintor.com.au</div>
</main>
</body>
</html>
```